QVR business card

Need a business card for a company that provides instructional design and elearning development services. The website is here: http://quorvane.studio/

I'm attaching a current logo, as well as the old business card design. While I like to keep it clean, the old design is too simplistic for my liking. The only idea I want to reuse from the old design is placing industry jargon on the back of the card, just need a better way to present it. But if you have other ideas for the back--feel free to experiment.

Please use the colors complementary to the color we have on the website. Thank you!

```html
<!DOCTYPE html>
<html lang="en">
<head>
<meta charset="utf-8">
<title>QVR business card</title>
<link rel="stylesheet" href="https://fonts.googleapis.com/css2?family=Open+Sans:wght@400;600;700;800&family=PT+Sans+Narrow:wght@400&display=swap">
<style>
  :root {
    --teal: #1db2b1;
    --teal-deep: #149f9f;
    --gold: #d8c68e;
    --ink: #2b2b2b;
    --ink-soft: #4a4a4a;
    --paper: #ffffff;
    --backdrop: #e9ecec;
  }
  * { box-sizing: border-box; margin: 0; padding: 0; }
  html, body {
    width: 1200px; height: 716px; overflow: hidden;
    background: var(--backdrop);
    font-family: "Open Sans", Arial, sans-serif;
  }
  .canvas {
    position: relative; width: 1200px; height: 716px;
    display: flex; align-items: center; justify-content: center; gap: 50px;
  }
  .card {
    position: relative; width: 525px; height: 300px; overflow: hidden;
    box-shadow: 0 6px 18px rgba(0,0,0,.18);
  }

  /* Front */
  .card-front { background: var(--paper); }
  .brand { position: absolute; left: 34px; top: 30px; display: flex; align-items: center; gap: 10px; }
  .brand-dot { width: 22px; height: 22px; border-radius: 50%; background: var(--gold); }
  .brand-name { font-weight: 700; font-size: 38px; line-height: 1; color: var(--teal); letter-spacing: .5px; }
  .person { position: absolute; left: 34px; top: 112px; }
  .person-name { font-weight: 700; font-size: 17px; color: var(--teal); }
  .person-role { font-size: 12px; color: var(--ink); margin-top: 2px; }
  .contacts { position: absolute; left: 34px; top: 170px; list-style: none; }
  .contacts li { display: flex; align-items: center; gap: 8px; font-size: 11.5px; color: var(--ink-soft); line-height: 22px; }
  .contacts svg { width: 12px; height: 12px; fill: var(--teal); flex: none; }
  .band-teal { position: absolute; left: 0; bottom: 0; width: 170px; height: 10px; background: var(--teal); }
  .band-gold { position: absolute; left: 170px; bottom: 0; right: 0; height: 10px; background: var(--gold); }
  .edge-teal { position: absolute; left: 0; bottom: 10px; width: 6px; height: 56px; background: var(--teal); }

  /* Back */
  .card-back { background: var(--teal); display: flex; align-items: center; padding: 0 30px 0 34px; }
  .question {
    color: var(--paper); font-weight: 800; font-size: 52px; line-height: .95;
    text-transform: uppercase; letter-spacing: -1px; padding-right: 22px;
    border-right: 2px solid rgba(255,255,255,.85);
  }
  .jargon { list-style: none; padding-left: 20px; }
  .jargon li {
    font-family: "PT Sans Narrow", "Arial Narrow", sans-serif;
    color: var(--paper); font-size: 27px; line-height: 1.18; text-transform: uppercase; white-space: nowrap;
  }
</style>
</head>
<body>
<main class="canvas">
  <section class="card card-front" aria-label="Card front">
    <div class="brand">
      <span class="brand-dot"></span>
      <span class="brand-name">QVR</span>
    </div>
    <div class="person">
      <p class="person-name">Mara Linwood</p>
      <p class="person-role">Managing Director</p>
    </div>
    <ul class="contacts">
      <li><svg viewBox="0 0 24 24"><path d="M6.6 10.8a15.1 15.1 0 0 0 6.6 6.6l2.2-2.2a1 1 0 0 1 1-.25 11.4 11.4 0 0 0 3.6.57 1 1 0 0 1 1 1V20a1 1 0 0 1-1 1A17 17 0 0 1 3 4a1 1 0 0 1 1-1h3.5a1 1 0 0 1 1 1c0 1.25.2 2.45.57 3.57a1 1 0 0 1-.25 1z"/></svg>555-014-2277</li>
      <li><svg viewBox="0 0 24 24"><path d="M2 5h20v14H2zm2 2v.5l8 5 8-5V7l-8 5z"/></svg>mlinwood@quorvane.studio</li>
      <li><svg viewBox="0 0 24 24"><path d="M12 2a10 10 0 1 0 0 20 10 10 0 0 0 0-20zm6.9 9h-3a15 15 0 0 0-1.3-5.6A8 8 0 0 1 18.9 11zM12 4.1c1 1.3 1.8 3.8 1.9 6.9h-3.8C10.2 7.9 11 5.4 12 4.1zM9.4 5.4A15 15 0 0 0 8.1 11h-3a8 8 0 0 1 4.3-5.6zM5.1 13h3a15 15 0 0 0 1.3 5.6A8 8 0 0 1 5.1 13zm6.9 6.9c-1-1.3-1.8-3.8-1.9-6.9h3.8c-.1 3.1-.9 5.6-1.9 6.9zm2.6-1.3a15 15 0 0 0 1.3-5.6h3a8 8 0 0 1-4.3 5.6z"/></svg>www.quorvane.studio</li>
    </ul>
    <span class="edge-teal"></span>
    <span class="band-teal"></span>
    <span class="band-gold"></span>
  </section>

  <section class="card card-back" aria-label="Card back">
    <h2 class="question">How<br>can<br>we<br>help?</h2>
    <ul class="jargon">
      <li>Mobile Learning SCORM</li>
      <li>Instructional Design LMS</li>
      <li>MOOCs eLearning HTML5</li>
      <li>Adult Learning Theory</li>
      <li>Gamification Classroom</li>
      <li>xAPI Blended Learning</li>
    </ul>
  </section>
</main>
</body>
</html>
```